Business card design for holistic health care clinic

We need a double-sided business card design for our holistic health care clinic that integrates our logo design and also its color scheme. My business is called Valmira. It is an integrative medicine clinic. You have already done the logo for me. Please ensure an elegant and upscale design that is not cluttered, but still has all the necessary information (please see below for details).

Target Market(s)

Wellness, fitness, rehabilitation for educated, well-traveled open-minded clients who are focused on natural, organic, balanced and preventive healthcare and lifestyle.

Industry/Entity Type

Medical

Contact Information for Business Card

Modern, clean.

Number of Pages Required

1 page

Font styles to use
Serif
Sans Serif

Colors

Designer to choose colors to be used in the design.

Requirements
Must have
• Logo on one side, all other information on the other side.
• Other information should include:
• Tobias Wrenfeld - DOE, CPT, LMT
• 4100 East Marrow Drive
• Austin, TX 78119
• 512 555 0148
• 818 555 0192
• info@ValmiraHealth.example
• t.wrenfeld@ValmiraHealth.example
Nice to have
• Darker background on front - but not totally black - shaded/dark gray.

```html
<!DOCTYPE html>
<html lang="en">
<head>
<meta charset="utf-8">
<title>Valmira Business Card</title>
<link rel="stylesheet" href="https://fonts.googleapis.com/css2?family=Nunito:wght@800&family=Roboto+Condensed:wght@700&family=Roboto:ital,wght@0,400;1,400&display=swap">
<style>
  :root {
    --backdrop: #5a4636;
    --card-dark: #272727;
    --card-light: #f1f1f1;
    --brand-blue: #0a8cc8;
    --text-light: #ececec;
    --text-muted: #4a4a4a;
    --rule: #8a8a8a;
  }
  * { margin: 0; padding: 0; box-sizing: border-box; }
  html, body { width: 1200px; height: 960px; overflow: hidden; }
  body { background: var(--backdrop); position: relative; font-family: "Roboto", sans-serif; }

  .card { position: absolute; width: 600px; height: 343px; border-radius: 18px; overflow: hidden; }
  .card-front { left: 314px; top: 113px; background: var(--card-dark); }
  .card-back { left: 311px; top: 472px; background: var(--card-light); }

  .front-brand {
    position: absolute; right: 36px; top: 40px;
    font-family: "Nunito", sans-serif; font-weight: 800; font-size: 64px;
    color: var(--brand-blue); letter-spacing: 1px;
  }
  .front-band { position: absolute; left: 447px; top: 200px; width: 40px; height: 143px; background: var(--brand-blue); }

  .holder { position: absolute; left: 38px; top: 172px; color: var(--brand-blue);
    font-family: "Roboto Condensed", sans-serif; font-weight: 700; font-size: 20px; }
  .holder .credentials { font-size: 12px; }

  .contact-list { position: absolute; left: 38px; top: 210px; list-style: none; }
  .contact-list li { display: flex; align-items: center; gap: 8px; height: 19.5px;
    font-size: 14.5px; color: var(--text-light); }
  .contact-list svg { width: 13px; height: 13px; fill: var(--brand-blue); flex: none; }
  .address { position: absolute; left: 38px; top: 295px; font-size: 14.5px; color: var(--text-light); }

  .brand-lockup { position: absolute; left: 0; right: 0; top: 130px; text-align: center; }
  .brand-mark { display: inline-block; width: 18px; height: 18px; border-radius: 50%;
    background: var(--brand-blue); margin-bottom: 6px; }
  .brand-name { font-family: "Nunito", sans-serif; font-weight: 800; font-size: 58px;
    line-height: 1; color: var(--brand-blue); letter-spacing: 1px; }
  .brand-sub { font-family: "Nunito", sans-serif; font-weight: 800; font-size: 17px;
    color: var(--brand-blue); margin-top: 4px; }

  .tagline { position: absolute; left: 85px; right: 95px; top: 272px; display: flex;
    align-items: center; gap: 8px; font-style: italic; font-size: 17px; color: var(--text-muted); }
  .tagline .rule { flex: 1; height: 1px; background: var(--rule); }
</style>
</head>
<body>
  <section class="card card-front">
    <div class="front-brand">Valmira</div>
    <div class="front-band"></div>
    <h1 class="holder">TOBIAS WRENFELD <span class="credentials">- DOE, CPT, LMT</span></h1>
    <ul class="contact-list">
      <li><svg viewBox="0 0 24 24"><path d="M6.6 10.8a15 15 0 0 0 6.6 6.6l2.2-2.2a1 1 0 0 1 1-.25 11.4 11.4 0 0 0 3.6.6 1 1 0 0 1 1 1V20a1 1 0 0 1-1 1A17 17 0 0 1 3 4a1 1 0 0 1 1-1h3.5a1 1 0 0 1 1 1c0 1.25.2 2.45.6 3.6a1 1 0 0 1-.25 1z"/></svg>512 555 0148</li>
      <li><svg viewBox="0 0 24 24"><path d="M7 1h10a2 2 0 0 1 2 2v18a2 2 0 0 1-2 2H7a2 2 0 0 1-2-2V3a2 2 0 0 1 2-2zm0 3v15h10V4z"/></svg>818 555 0192</li>
      <li><svg viewBox="0 0 24 24"><path d="M2 5h20v14H2zm2 2v.5l8 5 8-5V7z"/></svg>t.wrenfeld@ValmiraHealth.example</li>
      <li><svg viewBox="0 0 24 24"><circle cx="12" cy="12" r="10"/></svg>www.ValmiraHealth.example</li>
    </ul>
    <p class="address">4100 East Marrow Drive, Austin, TX 78119</p>
  </section>

  <section class="card card-back">
    <div class="brand-lockup">
      <span class="brand-mark"></span>
      <div class="brand-name">VALMIRA</div>
      <div class="brand-sub">Integrative Holistic Medicine</div>
    </div>
    <div class="tagline"><span class="rule"></span>helping the body help itself<span class="rule"></span></div>
  </section>
</body>
</html>
```